Website mockup using figma or other design software for Plumbing Company

We are looking for a talented UI/UX designer to create a high-converting, modern, and professional website design for a local plumbing company. The goal is to move away from the "dated" look of traditional trades and provide a seamless, trustworthy experience for homeowners and commercial clients.
The Challenge
Create a Homepage and a Service Page design that balances professional expertise with an urgent "call-to-action" (CTA) focus. We need a design that looks great on desktop but is built with a mobile-first mindset, as most customers find plumbers via their phones during emergencies.
This company will focus more on B2B, and corporate contracts, but should still be friendly to the public.
Here are some examples of what we are looking for
https://velotrin-works.com/construction/plumbing-construction/
https://velotrin-works.com/
The company is called "KT Plumbing."
Please see the logo below.

```html
<!DOCTYPE html>
<html lang="en">
<head>
<meta charset="utf-8">
<title>KT Plumbing — Reliable Plumbing Solutions</title>
<link href="https://fonts.googleapis.com/css2?family=Russo+One&family=Roboto:wght@400;500;700&display=swap" rel="stylesheet">
<style>
:root{
  --ink:#1f1f1f;
  --dark:#1c1c1c;
  --button:#474747;
  --text:#5b5b5b;
  --muted:#8a8a8a;
  --panel:#f2f2f2;
  --white:#ffffff;
  --line:#d9d9d9;
}
*{box-sizing:border-box;margin:0;padding:0}
html,body{width:1200px;height:4205px;overflow:hidden}
body{position:relative;background:var(--white);font-family:"Roboto",sans-serif;color:var(--ink)}
.abs{position:absolute}
.display{font-family:"Russo One",sans-serif;letter-spacing:1px}
.section-title{position:absolute;left:0;width:1200px;text-align:center;font-family:"Russo One",sans-serif;font-size:48px;color:#2b2b2b;text-shadow:2px 3px 4px rgba(0,0,0,.25);letter-spacing:1px}

/* buttons */
.btn{position:absolute;display:flex;align-items:center}
.btn-face{height:100%;display:flex;align-items:center;justify-content:center;font-weight:700;font-size:16px;clip-path:polygon(6% 0,100% 0,94% 100%,0 100%)}
.btn-dark .btn-face{background:var(--button);color:var(--white)}
.btn-light .btn-face{background:var(--white);color:var(--ink)}
.slashes{display:flex;gap:4px;margin-left:5px;height:100%}
.slashes i{display:block;width:4px;height:100%;transform:skewX(-14deg)}
.btn-dark .slashes i{background:var(--button)}
.btn-light .slashes i{background:var(--white)}

/* hero */
.hero{position:absolute;left:0;top:0;width:1200px;height:787px;
  background:linear-gradient(180deg,#1c1a18 0%,#3a352f 22%,#4a5560 36%,#2f6db3 55%,#3a82cc 66%,#2a4e7a 78%,#4b3f33 90%,#3a3129 100%)}
.logo{position:absolute;display:flex;align-items:center;gap:10px;font-family:"Roboto",sans-serif;font-weight:700}
.logo-dot{width:22px;height:22px;border-radius:50%;background:#cfcfcf}
.logo-name{color:#d6d6d6;font-size:30px;letter-spacing:1px}
.nav{position:absolute;top:66px;font-size:13px;font-weight:700;color:var(--white)}
.nav.active::after{content:"";position:absolute;left:0;right:0;top:22px;height:2px;background:var(--white)}
.hero-title{position:absolute;left:142px;top:240px;font-family:"Russo One",sans-serif;font-size:52px;line-height:60px;color:#f1f1f1;text-shadow:3px 3px 6px rgba(0,0,0,.6);letter-spacing:1px}
.hero-sub{position:absolute;left:143px;top:447px;font-size:23px;line-height:33px;font-weight:700;color:var(--white);text-shadow:1px 2px 4px rgba(0,0,0,.6)}

/* about */
.about-title{position:absolute;left:144px;top:895px;font-family:"Russo One",sans-serif;font-size:48px;color:#2b2b2b;text-shadow:2px 3px 4px rgba(0,0,0,.25)}
.about-copy{position:absolute;left:144px;top:972px;width:465px;font-size:14.5px;line-height:28px;color:var(--text);text-align:justify}

/* capabilities */
.cap-sub{position:absolute;left:0;width:1200px;top:1574px;text-align:center;font-size:16px;color:#444}
.cap-card{position:absolute;top:1654px;height:240px;clip-path:polygon(5% 0,100% 0,95% 100%,0 100%)}
.cap-label{position:absolute;top:1916px;width:300px;text-align:center;font-size:16.5px;font-weight:500;color:#333}
.round-arrow{position:absolute;width:36px;height:36px;border:2px solid #777;border-radius:50%}

/* gallery */
.tile{position:absolute;width:214px;height:242px;transform:skewX(-5deg)}

/* reviews */
.reviews{position:absolute;left:0;top:3013px;width:1200px;height:600px;background:var(--panel)}
.review{position:absolute;top:3230px;height:178px;background:var(--white);text-align:center;padding:22px 24px 0}
.review.featured{border:1px solid #cfcfcf;box-shadow:0 4px 10px rgba(0,0,0,.12)}
.review q{display:block;font-family:"Russo One",sans-serif;font-size:34px;line-height:30px;color:#333;quotes:none}
.review p{margin-top:14px;font-size:11.5px;line-height:22px;font-style:italic;color:var(--muted)}
.author{position:absolute;top:3435px;display:flex;align-items:center;gap:10px}
.avatar{width:42px;height:42px;border-radius:50%;background:linear-gradient(135deg,#c9a68a,#7c5f4c)}
.author b{display:block;font-size:15.5px;font-weight:500;color:#333}
.author span{display:block;font-size:10.5px;color:#555}

/* footer */
.footer-bg{position:absolute;left:0;top:3540px;width:1200px;height:665px}
.f-label{position:absolute;font-size:17px;font-weight:700;color:var(--white)}
.radio{position:absolute;top:3792px;display:flex;align-items:center;gap:6px;font-size:11.5px;color:#ddd}
.radio i{width:12px;height:12px;border:1.5px solid #ddd;border-radius:50%}
.field{position:absolute;border:1.5px solid #cfcfcf;font-size:14px;color:#eee;padding:5px 10px}
.submit{position:absolute;left:630px;top:3998px;width:84px;height:29px;background:var(--white);color:#222;font-size:11px;font-weight:700;display:flex;align-items:center;justify-content:center;clip-path:polygon(8% 0,100% 0,92% 100%,0 100%)}
.info{position:absolute;left:838px;font-size:13.5px;line-height:21px;color:#eee}
.info-icon{position:absolute;left:786px;width:34px;height:34px;border:1.5px solid #eee;border-radius:50%;display:flex;align-items:center;justify-content:center}
.social{position:absolute;top:3993px;width:28px;height:28px;border:1.5px solid #eee;border-radius:50%}
.social.filled{background:#eee}
.copyright{position:absolute;left:0;width:1200px;top:4140px;text-align:center;font-size:14px;color:#eee}
</style>
</head>
<body>

<!-- HERO -->
<section class="hero" role="img" aria-label="Photo of rows of blue industrial pipelines stretching across a dusky field"></section>
<div class="logo" style="left:144px;top:60px"><span class="logo-dot"></span><span class="logo-name">KT Plumbing</span></div>

<a class="nav active" style="left:511px">HOME</a>
<a class="nav" style="left:580px">ABOUT</a>
<a class="nav" style="left:655px">SERVICES</a>
<a class="nav" style="left:750px">CONTACT US</a>
<div class="btn btn-light" style="left:864px;top:51px;height:44px">
  <div class="btn-face" style="width:160px;font-size:13px">REQUEST SERVICE</div>
  <div class="slashes"><i></i><i></i><i></i></div>
</div>

<h1 class="hero-title">RELIABLE PLUMBING<br>SOLUTIONS FOR HOMES<br>&amp; BUSINESSES</h1>
<p class="hero-sub">Emergency repairs, commercial installations,<br>and long-term service contracts.</p>
<div class="btn btn-light" style="left:144px;top:552px;height:52px">
  <div class="btn-face" style="width:190px">REQUEST SERVICE</div>
  <div class="slashes"><i></i><i></i><i></i></div>
</div>
<svg class="abs" style="left:588px;top:676px" width="24" height="70" viewBox="0 0 24 70" fill="none" stroke="#fff" stroke-width="2">
  <rect x="2" y="2" width="20" height="36" rx="10"/><line x1="12" y1="9" x2="12" y2="16"/>
  <polyline points="4,46 12,54 20,46"/><polyline points="4,56 12,64 20,56"/>
</svg>

<!-- ABOUT -->
<svg class="abs" style="left:0;top:787px" width="1200" height="613" viewBox="0 0 1200 613">
  <polygon points="1000,6 1200,6 1080,330" fill="#e6e6e6"/>
  <polygon points="590,610 700,610 690,330" fill="#e6e6e6"/>
</svg>
<div class="abs" role="img" aria-label="Photo of stainless steel process piping and filtration vessels in an industrial plant"
  style="left:595px;top:793px;width:605px;height:603px;background:linear-gradient(160deg,#c9a24a 0%,#8e8c84 30%,#c9c9c6 55%,#6f7480 80%,#3d4452 100%);clip-path:polygon(0 0,67% 0,100% 100%,18% 100%)"></div>
<h2 class="about-title">ABOUT US</h2>
<p class="about-copy">KT Plumbing Division offers clients design, fabrication, and installation for commercial and industrial plumbing systems. As part of a MEP package or stand-alone, our team self-performs process piping, domestic water, medical gas, natural gas, waste/vent, and storm drainage systems.<br>Nemo enim ipsam voluptatem quia voluptas sit aspernatur aut odit aut fugit, sed quia consequuntur magni dolores eos qui ratione voluptatem sequi nesque porro quisquam</p>
<div class="btn btn-dark" style="left:144px;top:1230px;height:52px">
  <div class="btn-face" style="width:155px">READ MORE</div>
  <div class="slashes"><i></i><i></i><i></i></div>
</div>

<!-- CAPABILITIES -->
<svg class="abs" style="left:0;top:1400px" width="1200" height="750" viewBox="0 0 1200 750">
  <polygon points="32,4 1200,4 1200,0 1200,4 1172,4 1160,750 0,750 0,4" fill="#f2f2f2"/>
</svg>
<h2 class="section-title" style="top:1495px">OUR CAPABILITES</h2>
<p class="cap-sub">KT Plumbing can design, fabricate, and install any plumbing project need for our customers including:</p>
<div class="round-arrow" style="left:95px;top:1737px"></div>
<svg class="abs" style="left:95px;top:1737px" width="36" height="36" viewBox="0 0 36 36" fill="none" stroke="#666" stroke-width="2"><polyline points="21,11 14,18 21,25"/></svg>
<div class="round-arrow" style="left:1069px;top:1737px"></div>
<svg class="abs" style="left:1069px;top:1737px" width="36" height="36" viewBox="0 0 36 36" fill="none" stroke="#666" stroke-width="2"><polyline points="15,11 22,18 15,25"/></svg>

<div class="cap-card" role="img" aria-label="Photo of insulated medical gas pipework in a plant room" style="left:145px;width:300px;background:linear-gradient(135deg,#2a5fa8,#9fb8d4 45%,#e0a466 70%,#2c4a80)"></div>
<div class="abs" style="left:446px;top:1648px;width:306px;height:252px;background:var(--white);box-shadow:0 6px 14px rgba(0,0,0,.2);clip-path:polygon(5% 0,100% 0,95% 100%,0 100%)"></div>
<div class="cap-card" role="img" aria-label="Photo of laboratory gas regulators and gauges" style="left:454px;width:296px;background:linear-gradient(135deg,#4c5fb8,#7c7cc4 40%,#2f3f9a 70%,#c8a44a)"></div>
<div class="abs" style="left:560px;top:1734px;width:82px;height:82px;border-radius:50%;background:var(--white)"></div>
<svg class="abs" style="left:576px;top:1750px" width="50" height="50" viewBox="0 0 50 50" fill="none" stroke="#444" stroke-width="2.5">
  <circle cx="25" cy="14" r="8"/><line x1="25" y1="22" x2="25" y2="30"/>
  <rect x="10" y="30" width="30" height="10"/><line x1="4" y1="32" x2="4" y2="38"/><line x1="46" y1="32" x2="46" y2="38"/>
  <line x1="4" y1="35" x2="10" y2="35"/><line x1="40" y1="35" x2="46" y2="35"/>
</svg>
<div class="cap-card" role="img" aria-label="Photo of deionized water treatment tanks and pumps" style="left:754px;width:302px;background:linear-gradient(135deg,#7d8690,#cfd5da 40%,#2f5c9c 70%,#5b6470)"></div>
<p class="cap-label" style="left:145px">Medical Gas Systems</p>
<p class="cap-label" style="left:450px">Laboratory Air &amp; Gas Systems</p>
<p class="cap-label" style="left:754px">Deionized Water Systems</p>
<div class="btn btn-dark" style="left:503px;top:1987px;height:52px">
  <div class="btn-face" style="width:156px">VIEW MORE</div>
  <div class="slashes"><i></i><i></i><i></i></div>
</div>

<!-- PROJECT GALLERY -->
<h2 class="section-title" style="top:2250px">PROJECT GALLERY</h2>
<div class="tile" role="img" aria-label="Photo of a hand fitting a sink basin" style="left:170px;top:2351px;background:linear-gradient(135deg,#e6e4e0,#b9a99a)"></div>
<div class="tile" role="img" aria-label="Photo of a worker cutting copper pipe" style="left:393px;top:2351px;background:linear-gradient(135deg,#b06a3a,#6d4a3a 50%,#c9c2b8)"></div>
<div class="abs" style="left:480px;top:2454px;width:42px;height:42px;border:2px solid #fff;border-radius:50%;background:rgba(0,0,0,.35);color:#fff;font-size:26px;line-height:36px;text-align:center">+</div>
<div class="tile" role="img" aria-label="Photo of a plumber brazing copper pipe with a torch" style="left:616px;top:2351px;background:linear-gradient(135deg,#8a5a40,#d8642a 50%,#c8874a)"></div>
<div class="tile" role="img" aria-label="Photo of a worker in hi-vis gear assembling valves" style="left:839px;top:2351px;background:linear-gradient(135deg,#8a8f7a,#7db83a 45%,#4f5560)"></div>
<div class="tile" role="img" aria-label="Photo of a filtration unit with blue water lines" style="left:143px;top:2603px;background:linear-gradient(135deg,#d6d8da,#8e9498 50%,#3aa8c8)"></div>
<div class="tile" role="img" aria-label="Photo of a pressure gauge on a steel manifold" style="left:366px;top:2603px;background:linear-gradient(135deg,#c3c8cc,#7a8086 55%,#dfe2e4)"></div>
<div class="tile" role="img" aria-label="Photo of a plumber in safety glasses soldering pipe" style="left:589px;top:2603px;background:linear-gradient(135deg,#5a5e66,#e8a030 50%,#d85a2a)"></div>
<div class="tile" role="img" aria-label="Photo of wall mounted gas regulators with blue tubing" style="left:812px;top:2603px;background:linear-gradient(135deg,#e6e6e4,#c9ccce 50%,#4a88c8)"></div>
<div class="btn btn-dark" style="left:503px;top:2884px;height:52px">
  <div class="btn-face" style="width:156px">VIEW MORE</div>
  <div class="slashes"><i></i><i></i><i></i></div>
</div>

<!-- CUSTOMER REVIEWS -->
<section class="reviews"></section>
<h2 class="section-title" style="top:3118px">CUSTOMER REVIEWS</h2>
<div class="round-arrow" style="left:78px;top:3308px"></div>
<svg class="abs" style="left:78px;top:3308px" width="36" height="36" viewBox="0 0 36 36" fill="none" stroke="#666" stroke-width="2"><polyline points="21,11 14,18 21,25"/></svg>
<div class="round-arrow" style="left:1086px;top:3308px"></div>
<svg class="abs" style="left:1086px;top:3308px" width="36" height="36" viewBox="0 0 36 36" fill="none" stroke="#666" stroke-width="2"><polyline points="15,11 22,18 15,25"/></svg>

<div class="review" style="left:135px;width:301px"><q>&ldquo;</q><p>Fast response, clean work and honest pricing. The crew fixed our main line in one visit and explained every step along the way.</p></div>
<div class="review featured" style="left:449px;width:306px"><q>&ldquo;</q><p>Fast response, clean work and honest pricing. The crew fixed our main line in one visit and explained every step along the way.</p></div>
<svg class="abs" style="left:592px;top:3407px" width="20" height="11" viewBox="0 0 20 11"><polygon points="0,0 20,0 10,10" fill="#fff" stroke="#cfcfcf"/><line x1="0" y1="0.5" x2="20" y2="0.5" stroke="#fff" stroke-width="2"/></svg>
<div class="review" style="left:769px;width:297px"><q>&ldquo;</q><p>Fast response, clean work and honest pricing. The crew fixed our main line in one visit and explained every step along the way.</p></div>

<div class="author" style="left:210px"><div class="avatar" role="img" aria-label="Customer portrait"></div><div><b>Dana Morrow</b><span>Client</span></div></div>
<div class="author" style="left:522px"><div class="avatar" role="img" aria-label="Customer portrait"></div><div><b>Elena Voss</b><span>Client</span></div></div>
<div class="author" style="left:846px"><div class="avatar" role="img" aria-label="Customer portrait"></div><div><b>Marco Delvane</b><span>Client</span></div></div>

<!-- FOOTER -->
<svg class="footer-bg" viewBox="0 0 1200 665" preserveAspectRatio="none">
  <defs><linearGradient id="footShade" x1="0" y1="0" x2="1" y2="1"><stop offset="0" stop-color="#181818"/><stop offset=".6" stop-color="#222"/><stop offset="1" stop-color="#2e2e2e"/></linearGradient></defs>
  <path d="M0,70 Q600,-20 1200,40 L1200,665 L0,665 Z" fill="url(#footShade)"/>
</svg>
<div class="logo" style="left:521px;top:3660px"><span class="logo-dot"></span><span class="logo-name">KT Plumbing</span></div>

<p class="f-label" style="left:172px;top:3788px">Get In Touch:</p>
<label class="radio" style="left:356px"><i></i>General</label>
<label class="radio" style="left:437px"><i></i>Estimating</label>
<label class="radio" style="left:536px"><i></i>Service</label>
<div class="field" style="left:173px;top:3833px;width:266px;height:30px">Name :</div>
<div class="field" style="left:449px;top:3833px;width:266px;height:30px">Phone :</div>
<div class="field" style="left:173px;top:3873px;width:542px;height:30px">Email :</div>
<div class="field" style="left:173px;top:3912px;width:542px;height:68px">Message :</div>
<div class="submit">SUBMIT</div>

<p class="f-label" style="left:786px;top:3788px">Contact Information</p>
<div class="info-icon" style="top:3836px"><svg width="14" height="18" viewBox="0 0 14 18"><path d="M7 0C3 0 0 3 0 7c0 5 7 11 7 11s7-6 7-11c0-4-3-7-7-7z" fill="#eee"/><circle cx="7" cy="7" r="2.5" fill="#1c1c1c"/></svg></div>
<p class="info" style="top:3828px">4820 Harlow Ridge Road<br>Ashford, CA 95710<br>212 Copperline Drive<br>Renwick, NV 89120</p>
<div class="info-icon" style="top:3922px"><svg width="16" height="16" viewBox="0 0 24 24" fill="none" stroke="#eee" stroke-width="2"><path d="M5 3h4l2 5-3 2a12 12 0 0 0 6 6l2-3 5 2v4a2 2 0 0 1-2 2A18 18 0 0 1 3 5a2 2 0 0 1 2-2z"/></svg></div>
<p class="info" style="top:3925px">General Inquiries: 555-210-4400<br>Service Department: 555-210-4471</p>
<span class="social" style="left:787px"></span>
<span class="social filled" style="left:822px"></span>
<span class="social" style="left:856px"></span>
<span class="social" style="left:890px"></span>
<span class="social" style="left:924px"></span>

<div class="abs" style="left:173px;top:4085px;width:892px;height:1px;background:#444"></div>
<p class="copyright">Copyrights © 2026 Companyname. All Rights Reserved. &nbsp;|&nbsp; Privacy Policy &nbsp;|&nbsp; Terms of Use</p>

</body>
</html>
```